Make it cool to work near where you are...

Calling all creatives - create the ultimate cool card for people who want to cut their commute.

Here at PineNook we've got what can best be described as an Flintpass card for desks - and we want to brighten up the wallets of our most loyal users.

So, pitch us your ideas and you might see your design on cards being flashed across the country - and we've thrown in a bit of cash too.

Do see our brief card guidelines - with a couple of past examples thrown in.

```html
<!DOCTYPE html>
<html lang="en">
<head>
<meta charset="utf-8">
<title>PineNook Business Card</title>
<link href="https://fonts.googleapis.com/css2?family=Lato:wght@400;700;900&display=swap" rel="stylesheet">
<style>
  :root {
    --backdrop: #dce5eb;
    --charcoal: #3b3b3b;
    --magenta: #e4287e;
    --stone: #bdbaba;
    --paper: #f6f6f6;
    --ink: #2f2f2f;
  }
  * { margin: 0; padding: 0; box-sizing: border-box; }
  html, body { width: 1200px; height: 960px; overflow: hidden; }
  body {
    background: var(--backdrop);
    font-family: "Lato", Arial, sans-serif;
    position: relative;
  }
  .card {
    position: absolute;
    left: 285px;
    width: 630px;
    height: 358px;
    border-radius: 22px;
    overflow: hidden;
    background: var(--paper);
  }
  .card-front { top: 95px; background: var(--charcoal); }
  .card-back { top: 507px; }
  .card-art { position: absolute; inset: 0; width: 630px; height: 358px; }

  .front-wordmark {
    position: absolute;
    left: 58px;
    top: 78px;
    display: flex;
    align-items: center;
    gap: 16px;
  }
  .front-wordmark .mark-square {
    width: 26px; height: 26px; background: var(--magenta);
  }
  .front-wordmark .name {
    font-weight: 900;
    font-size: 76px;
    color: #fff;
    letter-spacing: -1px;
    line-height: 1;
  }
  .front-url {
    position: absolute;
    left: 58px;
    top: 294px;
    font-weight: 700;
    font-size: 19px;
    color: #fff;
  }

  .back-content {
    position: absolute;
    left: 288px;
    top: 52px;
    color: var(--ink);
  }
  .back-wordmark {
    display: flex;
    align-items: center;
    gap: 8px;
  }
  .back-wordmark .mark-dot {
    width: 14px; height: 14px; border-radius: 50%; background: var(--magenta);
  }
  .back-wordmark .name {
    font-weight: 900;
    font-size: 34px;
    color: var(--magenta);
    letter-spacing: -0.5px;
    line-height: 1;
  }
  .person-name {
    margin-top: 52px;
    font-weight: 900;
    font-size: 19px;
    color: var(--magenta);
    line-height: 1.1;
  }
  .person-role { font-size: 15px; line-height: 1.25; }
  .contact-list { list-style: none; margin-top: 22px; font-size: 15px; }
  .contact-list li { display: flex; align-items: center; gap: 8px; height: 18px; }
  .contact-list svg { width: 16px; height: 16px; flex: none; }
  .address { margin-top: 16px; font-size: 15px; line-height: 1.2; }
</style>
</head>
<body>

<section class="card card-front">
  <svg class="card-art" viewBox="0 0 630 358" aria-hidden="true">
    <polygon fill="var(--stone)" points="430,358 630,158 630,172 444,358"/>
    <polygon fill="var(--magenta)" points="470,358 630,198 630,358"/>
  </svg>
  <div class="front-wordmark">
    <span class="name">PineNook</span>
    <span class="mark-square"></span>
  </div>
  <div class="front-url">www.PineNook.com</div>
</section>

<section class="card card-back">
  <svg class="card-art" viewBox="0 0 630 358" aria-hidden="true">
    <rect fill="var(--charcoal)" x="0" y="0" width="200" height="358"/>
    <rect fill="var(--magenta)" x="200" y="0" width="10" height="358"/>
    <rect fill="var(--stone)" x="222" y="0" width="4" height="358"/>
  </svg>
  <div class="back-content">
    <div class="back-wordmark">
      <span class="name">PineNook</span>
      <span class="mark-dot"></span>
    </div>
    <h1 class="person-name">JANE ROWE</h1>
    <p class="person-role">Managing Director</p>
    <ul class="contact-list">
      <li>
        <svg viewBox="0 0 16 16" aria-hidden="true"><path fill="var(--magenta)" d="M1,5 C1,2 15,2 15,5 L12,6 L11,4.5 H5 L4,6 Z M4,7 H12 L14,13 H2 Z"/></svg>
        <span>+44 20 7946 0182</span>
      </li>
      <li>
        <svg viewBox="0 0 16 16" aria-hidden="true"><rect x="1" y="3" width="14" height="10" fill="var(--magenta)"/><path d="M1.5,3.5 L8,9 L14.5,3.5" stroke="#fff" stroke-width="1.3" fill="none"/></svg>
        <span>team@pinenook.com</span>
      </li>
      <li>
        <svg viewBox="0 0 16 16" aria-hidden="true"><circle cx="8" cy="8" r="6.5" fill="none" stroke="var(--magenta)" stroke-width="1.5"/><ellipse cx="8" cy="8" rx="2.8" ry="6.5" fill="none" stroke="var(--magenta)" stroke-width="1.2"/><path d="M1.5,8 H14.5 M2.5,5 H13.5 M2.5,11 H13.5" stroke="var(--magenta)" stroke-width="1.1"/></svg>
        <span>www.pinenook.com</span>
      </li>
    </ul>
    <p class="address">NookHouse, 48-52 Alder Lane<br>E2 7QX London, United Kingdom</p>
  </div>
</section>

</body>
</html>
```